One Page Website for Personal Trainer in London

I have a logo and need a one page website designed around my branding. I am a freelance Personal Trainer based in London specialising in bodyweight training for men and women. I would like the site to be modern and clean but not overtly urban in design.
I need the following headings:
About Me
My Services
Events
Blog
I don't need them to be seperate pages but if they can link to further down the page that would be great.
Industry/Entity Type
Personal Trainer
Coding
Coded - Design and coding required
Number of Pages Required
1 page
Requirements
Must have
- I need the following headings:
- About Me
- My Services
- Events
- Blog
- mobile friendly formatting
- health and fitness related photography
- Colour scheme in keeping with my existing logo

```html
<!DOCTYPE html>
<html lang="en">
<head>
<meta charset="utf-8">
<title>Marlow Reed Personal Training</title>
<link href="https://fonts.googleapis.com/css2?family=Open+Sans:wght@400;600;700;800&family=PT+Serif&display=swap" rel="stylesheet">
<style>
:root{
  --orange:#f7931e;
  --ink:#2b2b2b;
  --dark:#2f2f2f;
  --footer:#3d3d3d;
  --grey:#8a8a8a;
  --line:#d6d6d6;
  --light:#f2f2f2;
  --white:#ffffff;
}
*{margin:0;padding:0;box-sizing:border-box}
html,body{width:1200px;height:3340px;overflow:hidden}
body{font-family:"Open Sans",Arial,sans-serif;color:var(--ink);background:var(--white);position:relative}
section,header,footer{position:absolute;left:0;width:1200px}
.abs{position:absolute}
.top-strip{top:0;height:11px;background:var(--dark);width:1200px;position:absolute}

/* header */
.site-header{top:11px;height:116px;background:var(--white)}
.brand{left:56px;top:30px;display:flex;align-items:center;gap:10px}
.brand-dot{width:30px;height:30px;border-radius:50%;background:var(--orange)}
.brand-name{font-size:26px;font-weight:700;color:var(--orange);letter-spacing:.3px}
.header-phone{left:819px;top:22px;display:flex;align-items:center;gap:10px;font-size:21px;font-weight:600;color:var(--ink)}
.main-nav{left:721px;top:75px;display:flex;gap:10px;font-size:11.5px;font-weight:600;color:var(--ink)}
.main-nav a{color:inherit;text-decoration:none}
.main-nav a.active{color:var(--orange);border-bottom:1px solid var(--orange)}
.main-nav .sep{color:#999}

/* hero */
.hero{top:127px;height:572px;overflow:hidden}
.hero-photo{position:absolute;inset:0;background:
  radial-gradient(ellipse at 25% 10%,#f6e7a0 0%,#d7b955 22%,rgba(150,140,70,.6) 45%,rgba(0,0,0,0) 70%),
  linear-gradient(180deg,#9a8c4d 0%,#8a8466 40%,#76746e 65%,#5f5e5c 100%)}
.hero-copy{left:60px;width:460px;top:180px;text-align:center}
.hero-lead{font-size:44px;color:#2a2a2a;font-weight:400;line-height:1}
.hero-title{font-size:54px;font-weight:800;color:#1f1f1f;line-height:1;margin-top:10px;letter-spacing:.5px}
.hero-sub{font-size:25px;color:#1f1f1f;margin-top:4px}
.hero-btn{display:inline-block;margin-top:20px;width:227px;height:54px;line-height:54px;text-align:center;background:var(--orange);color:var(--white);font-size:18px}

/* headings */
.sec-title{width:1200px;text-align:center;font-size:30px;font-weight:700}
.sec-title .hl{color:var(--orange)}
.rule{left:73px;width:1051px;height:1px}
.rule-mark{left:591px;width:18px;height:18px;border-radius:50%}

/* about */
.about{top:699px;height:481px;background:var(--white)}
.about .sec-title{top:52px;color:var(--ink)}
.about .rule{top:118px;background:var(--line)}
.about .rule-mark{top:109px;background:var(--orange)}
.about-lead{left:170px;width:860px;top:180px;text-align:center;font-size:14px;font-weight:600;line-height:20px;text-transform:uppercase}
.about-text{left:200px;width:800px;top:236px;text-align:center;font-size:12.5px;line-height:21px;color:var(--grey)}
.btn-small{height:36px;line-height:36px;text-align:center;background:var(--orange);color:var(--white);font-size:11px;font-weight:600;width:150px;left:525px}
.about .btn-small{top:381px}

/* services */
.services{top:1180px;height:645px;background:linear-gradient(180deg,#2c2c2c,#333 50%,#2b2b2b)}
.services .sec-title{top:56px;color:var(--white)}
.services .rule{top:136px;background:#6a6a6a}
.services .rule-mark{top:127px;background:#8a8a8a}
.service{top:193px;width:260px;text-align:center}
.service-photo{width:216px;height:216px;border-radius:50%;margin:0 auto;border:5px solid var(--white)}
.service-photo.active{border-color:var(--orange)}
.service-name{margin-top:20px;color:var(--orange);font-size:16px;font-weight:700}
.services .btn-small{top:514px}

/* blog */
.blog{top:1825px;height:713px;background:var(--orange)}
.blog .sec-title{top:58px;color:var(--white);font-size:40px}
.blog-bar{left:585px;top:137px;width:30px;height:3px;background:var(--white)}
.post{top:187px;width:267px;height:328px;background:var(--white);border-radius:4px;overflow:hidden}
.post-photo{height:187px;position:relative}
.post-date{position:absolute;left:0;top:0;width:44px;height:48px;background:var(--orange);color:var(--white);text-align:center}
.post-date b{display:block;font-size:22px;line-height:28px}
.post-date span{display:block;font-size:7px}
.post-body{padding:16px 14px}
.post-title{font-size:15px;font-weight:600;line-height:19px;color:#222}
.post-excerpt{margin-top:12px;font-size:10.5px;line-height:14px;color:#666}
.all-posts{left:525px;top:599px;display:flex;height:36px}
.all-posts span{width:169px;background:#e8e8e8;color:#777;font-size:10.5px;font-weight:600;line-height:36px;text-align:center}
.all-posts i{width:32px;background:#333}

/* events & testimonials */
.lower{top:2538px;height:423px;background:var(--light)}
.col-title{font-size:28px;font-weight:600;color:var(--orange);top:60px}
.arrows{top:68px;display:flex;gap:6px}
.arrows svg{display:block}
.col-rule{top:119px;height:1px;background:#bdbdbd}
.col-divider{left:603px;top:120px;width:1px;height:240px;background:#dcdcdc}
.event{left:98px;width:462px;display:flex;gap:38px}
.event-date{width:58px;text-align:center;color:var(--white);flex:none}
.event-date b{display:block;height:48px;line-height:48px;background:#333;font-size:22px}
.event-date span{display:block;height:30px;line-height:30px;background:var(--orange);font-size:14px}
.event-title{font-size:15px;font-weight:600;margin-top:6px}
.event-text{margin-top:10px;font-size:11.5px;line-height:16px;color:#777}
.event-sep{left:98px;width:462px;top:244px;height:1px;background:#d9d9d9}
.client-photo{left:663px;top:142px;width:138px;height:138px;border-radius:50%;border:4px solid var(--white);background:linear-gradient(160deg,#e4ddd4,#c9b7a4 55%,#d98b9b)}
.client-name{left:663px;width:138px;top:292px;text-align:center;font-size:12px;color:var(--orange);font-weight:600}
.quote{left:835px;top:146px;width:290px;font-size:11.5px;line-height:17px;color:#666;text-align:justify}
.quote .mark{color:var(--orange);font-size:22px;font-weight:700;line-height:0;vertical-align:-6px}

/* footer */
.site-footer{top:2961px;height:323px;background:var(--footer);color:var(--white)}
.foot-brand{left:95px;top:55px;display:flex;align-items:center;gap:8px}
.foot-brand .brand-dot{width:22px;height:22px;background:var(--white)}
.foot-brand .brand-name{color:var(--white);font-size:22px}
.foot-about{left:70px;top:150px;width:240px;font-size:11px;line-height:15px;color:#e6e6e6}
.foot-div{top:66px;width:1px;height:190px;background:#6c6c6c}
.foot-head{font-size:17px;font-weight:600;letter-spacing:.5px;top:70px}
.foot-head .hl{color:var(--orange)}
.foot-head-rule{top:102px;height:1px;background:#6c6c6c}
.quick-links{left:403px;top:120px;list-style:none;font-size:13px;line-height:26px}
.quick-links li::before{content:"• ";color:#ccc}
.contact-list{left:628px;top:126px;font-size:11px;line-height:18px;color:#e6e6e6}
.contact-list .row{display:flex;align-items:center;gap:8px}
.social{left:897px;top:120px;display:flex;gap:12px}
.social i{display:block;width:18px;height:18px;border:2px solid var(--white);border-radius:50%}
.call-label{left:897px;top:196px;font-size:14px;font-weight:700}
.call-number{left:897px;top:220px;font-family:"PT Serif",Georgia,serif;font-size:25px}
.call-rule{left:897px;top:178px;width:18px;height:1px;background:#999}
.bottom-bar{top:3284px;height:56px;background:var(--orange);color:var(--white);font-size:12px;text-align:center;line-height:56px}
</style>
</head>
<body>
<div class="top-strip"></div>

<header class="site-header">
  <div class="abs brand"><span class="brand-dot"></span><span class="brand-name">Marlow Reed</span></div>
  <div class="abs header-phone">
    <svg width="24" height="24" viewBox="0 0 24 24"><circle cx="12" cy="12" r="11" fill="none" stroke="#f7931e" stroke-width="2"/><path d="M8.5 6.5l2 2.2-1.2 1.4c.7 1.6 2 2.9 3.6 3.6l1.4-1.2 2.2 2-1.3 1.9c-4-.6-7.9-4.5-8.5-8.5z" fill="#f7931e"/></svg>
    <span>(555) 014 2287</span>
  </div>
  <nav class="abs main-nav">
    <a href="#top" class="active">HOME</a><span class="sep">|</span>
    <a href="#about">ABOUT ME</a><span class="sep">|</span>
    <a href="#services">MY SERVICES</a><span class="sep">|</span>
    <a href="#events">EVENTS</a><span class="sep">|</span>
    <a href="#blog">BLOG</a>
  </nav>
</header>

<section class="hero" id="top">
  <div class="hero-photo" role="img" aria-label="Runner lacing a bright running shoe on a sunlit autumn road"></div>
  <div class="abs hero-copy">
    <div class="hero-lead">Start adding</div>
    <div class="hero-title">BODY WEIGHT<br>MOVEMENTS</div>
    <div class="hero-sub">into your training &amp; enjoy the results!</div>
    <div class="hero-btn">Start training Now</div>
  </div>
</section>

<section class="about" id="about">
  <h2 class="abs sec-title"><span class="hl">About</span> us</h2>
  <div class="abs rule"></div><div class="abs rule-mark"></div>
  <p class="abs about-lead">Strength you build with your own body stays with you for life. Train smarter, move better and feel the difference every single day</p>
  <p class="abs about-text">I help busy men and women in London build real strength using nothing but their own bodyweight. Every session is planned around your goals, your schedule and your current level, so you progress safely and steadily. Whether you want to lose fat, move better or simply feel more confident, we will work together on simple movements done well. Training can happen outdoors in the park, at your home or at a studio nearby, and each plan comes with clear guidance you can follow between sessions, so the progress keeps going all week.</p>
  <div class="abs btn-small">READ MORE</div>
</section>

<section class="services" id="services">
  <h2 class="abs sec-title"><span class="hl">Our</span> Service</h2>
  <div class="abs rule"></div><div class="abs rule-mark"></div>
  <div class="abs service" style="left:55px">
    <div class="service-photo active" role="img" aria-label="Woman stretching in a lunge by the sea" style="background:linear-gradient(180deg,#b9cfe0,#8fa6b8 60%,#5a6470)"></div>
    <div class="service-name">Stretching</div>
  </div>
  <div class="abs service" style="left:313px">
    <div class="service-photo" role="img" aria-label="Woman doing a bodyweight exercise with a dumbbell" style="background:linear-gradient(160deg,#d9d4cf,#a9a09b 55%,#6c5d7a)"></div>
    <div class="service-name">Bodyweight Exercise</div>
  </div>
  <div class="abs service" style="left:578px">
    <div class="service-photo" role="img" aria-label="Trainers, dumbbells and a towel laid out for a workout" style="background:linear-gradient(160deg,#4a78b5,#6c8fbf 45%,#e86a9a)"></div>
    <div class="service-name">Fitness Plans</div>
  </div>
  <div class="abs service" style="left:858px">
    <div class="service-photo" role="img" aria-label="Trainer guiding a client in the gym" style="background:linear-gradient(160deg,#e8e3de,#b8aaa0 55%,#5b4d47)"></div>
    <div class="service-name">Personal Training</div>
  </div>
  <div class="abs btn-small">MORE SERVICE</div>
</section>

<section class="blog" id="blog">
  <h2 class="abs sec-title">Latest Blog</h2>
  <div class="abs blog-bar"></div>
  <article class="abs post" style="left:42px">
    <div class="post-photo" role="img" aria-label="Woman resting between push ups" style="background:linear-gradient(135deg,#cfe2ec,#a9c3d1 50%,#d6a28f)"><div class="post-date"><b>22</b><span>October</span></div></div>
    <div class="post-body"><h3 class="post-title">Five warm up moves before every session</h3><p class="post-excerpt">Simple warm up routines that prepare your joints and muscles before every bodyweight session.</p></div>
  </article>
  <article class="abs post" style="left:325px">
    <div class="post-photo" role="img" aria-label="Couple running together outdoors" style="background:linear-gradient(135deg,#f1e4c8,#c9b07a 50%,#7a6a55)"><div class="post-date"><b>23</b><span>October</span></div></div>
    <div class="post-body"><h3 class="post-title">Why short daily workouts beat long ones</h3><p class="post-excerpt">Why short daily sessions often beat long weekly workouts for lasting strength gains.</p></div>
  </article>
  <article class="abs post" style="left:610px">
    <div class="post-photo" role="img" aria-label="Group fitness class lifting light dumbbells" style="background:linear-gradient(135deg,#cde2ea,#9fc1cf 50%,#a58bb8)"><div class="post-date"><b>24</b><span>October</span></div></div>
    <div class="post-body"><h3 class="post-title">Pairing push ups and rows for balance at home</h3><p class="post-excerpt">How to pair push ups and rows for a balanced upper body routine at home.</p></div>
  </article>
  <article class="abs post" style="left:893px">
    <div class="post-photo" role="img" aria-label="Running shoes on a sunlit field path" style="background:linear-gradient(160deg,#f6d98a,#e0a84c 50%,#8a6a3a)"><div class="post-date"><b>25</b><span>October</span></div></div>
    <div class="post-body"><h3 class="post-title">Running form tips that protect your knees</h3><p class="post-excerpt">Small changes to your stride that help you run further and enjoy every mile.</p></div>
  </article>
  <div class="abs all-posts"><span>VIEW ALL BLOG POSTS</span><i></i></div>
</section>

<section class="lower" id="events">
  <h2 class="abs col-title" style="left:93px">Events</h2>
  <div class="abs arrows" style="left:514px">
    <svg width="18" height="18" viewBox="0 0 18 18"><circle cx="9" cy="9" r="9" fill="#f7931e"/><path d="M10.5 5.5L7 9l3.5 3.5" stroke="#fff" stroke-width="2" fill="none"/></svg>
    <svg width="18" height="18" viewBox="0 0 18 18"><circle cx="9" cy="9" r="9" fill="#f7931e"/><path d="M7.5 5.5L11 9l-3.5 3.5" stroke="#fff" stroke-width="2" fill="none"/></svg>
  </div>
  <div class="abs col-rule" style="left:93px;width:467px"></div>
  <div class="abs event" style="top:153px">
    <div class="event-date"><b>30</b><span>Oct</span></div>
    <div><h3 class="event-title">Bodyweight bootcamp in the park</h3><p class="event-text">A friendly outdoor group session for every level. Bring water, a mat and plenty of energy.</p></div>
  </div>
  <div class="abs event-sep"></div>
  <div class="abs event" style="top:258px">
    <div class="event-date"><b>31</b><span>Oct</span></div>
    <div><h3 class="event-title">Mobility and stretching workshop</h3><p class="event-text">An hour of guided stretching to ease stiff joints and improve posture. Spaces are limited.</p></div>
  </div>
  <div class="abs col-divider"></div>

  <h2 class="abs col-title" style="left:661px">Testimonials</h2>
  <div class="abs arrows" style="left:1078px">
    <svg width="18" height="18" viewBox="0 0 18 18"><circle cx="9" cy="9" r="9" fill="#f7931e"/><path d="M10.5 5.5L7 9l3.5 3.5" stroke="#fff" stroke-width="2" fill="none"/></svg>
    <svg width="18" height="18" viewBox="0 0 18 18"><circle cx="9" cy="9" r="9" fill="#f7931e"/><path d="M7.5 5.5L11 9l-3.5 3.5" stroke="#fff" stroke-width="2" fill="none"/></svg>
  </div>
  <div class="abs col-rule" style="left:661px;width:463px"></div>
  <div class="abs client-photo" role="img" aria-label="Portrait of a smiling client"></div>
  <div class="abs client-name">HANNAH</div>
  <p class="abs quote"><span class="mark">“</span> I had never trained without machines before, and I was not sure bodyweight work would be enough. Three months later I am stronger, sleeping better and I can finally do full push ups. Every session is different, the plans are easy to follow at home and the encouragement never stops. I would recommend it to anyone. <span class="mark">”</span></p>
</section>

<footer class="site-footer">
  <div class="abs foot-brand"><span class="brand-dot"></span><span class="brand-name">Marlow Reed</span></div>
  <p class="abs foot-about">Bodyweight personal training for men and women across London. Sessions in the park, at home or in the studio, built around your goals and your week.</p>
  <div class="abs foot-div" style="left:356px"></div>
  <div class="abs foot-div" style="left:583px"></div>
  <div class="abs foot-div" style="left:857px"></div>

  <h3 class="abs foot-head" style="left:403px">QUICK LINKS</h3>
  <div class="abs foot-head-rule" style="left:403px;width:138px"></div>
  <ul class="abs quick-links">
    <li>Home</li><li>About Us</li><li>services</li><li>Events</li><li>Blogs</li><li>Contact</li>
  </ul>

  <h3 class="abs foot-head" style="left:628px">CONTACT</h3>
  <div class="abs foot-head-rule" style="left:628px;width:190px"></div>
  <div class="abs contact-list">
    <div>42 Elm Row<br>Westbury, IL 60100</div>
    <div class="row" style="margin-top:10px"><svg width="10" height="10" viewBox="0 0 24 24"><path d="M5 3l4 4-2 3c1.5 3 4 5.5 7 7l3-2 4 4-3 3C9 21 3 15 2 6z" fill="#fff"/></svg>555-017-3390</div>
    <div class="row"><svg width="10" height="10" viewBox="0 0 24 24"><path d="M5 3l4 4-2 3c1.5 3 4 5.5 7 7l3-2 4 4-3 3C9 21 3 15 2 6z" fill="#fff"/></svg>555-016-4412</div>
    <div class="row"><svg width="10" height="10" viewBox="0 0 24 24"><rect x="2" y="5" width="20" height="14" fill="#fff"/><path d="M2 5l10 8 10-8" stroke="#3d3d3d" stroke-width="2" fill="none"/></svg>hello@marlowreedfit.com</div>
    <div class="row"><svg width="10" height="10" viewBox="0 0 24 24"><circle cx="12" cy="12" r="10" fill="#fff"/></svg>www.marlowreedfit.com</div>
  </div>

  <h3 class="abs foot-head" style="left:897px">FOLLOW US <span class="hl">ON</span></h3>
  <div class="abs social" aria-label="Social profiles"><i></i><i></i><i></i><i></i></div>
  <div class="abs call-rule"></div>
  <div class="abs call-label">CALL US ON</div>
  <div class="abs call-number">555-017-3390</div>
</footer>

<div class="abs bottom-bar" style="left:0;width:1200px">© marlowreed &nbsp;|&nbsp; Privacy Policy &nbsp;|&nbsp; User Agreement</div>
</body>
</html>
```